Thoroughbred Racing Partnership needs web design

Glimmer of Laurel Partners is a management group who buys horses and races them on both the West and East coasts. The premise of the business is for an investment as little as $500, anyone can be a partner and own a percentage of a horse(s). This is a low cost way of getting involved in the exciting sport of Thoroughbred Racing, without shouldering the heavy financial responsibility. Our target market is mostly males 40+ but we want to include all target markets. We are looking for something very clean and professional, we want to give an image of success. Nothing overly "artsy." I have included the logo in which you can incorporate in the site. Also, the logo colors will be the colors of our "silks." The silks are what the jockey wears and will be an important marketing tool for GOL. We would like a very prominent picture of a racehorse somewhere on the homepage, we want to make it clear that is a website for Horseracing partnerships.

On the top of the site, it should say "Glimmer of Laurel" (on the top)
and below that "Thoroughbred Racing Partnerships." (below that)

The main sections, which should be across the top are:

Home
About Us
Ownership
Stable Roster
News
Contact us

Some of these will have drop down menus.

An example of a competitor website that we like is: www.harrowgatefarm.example
An example of a competitor website that we don't like is: www.paddockvue.example
Updates

Project Deadline Extended
Reason: We have a Board of Directors meeting on the 22nd and we will be making a decision on that day. I'm giving an extension so that all designers are able to submit their designs by the 22nd. Thank you!

Target Market(s)

40+ males

Industry/Entity Type

Business

Requirements
Must have
• our logo must be on the site. We would like at least one bold image of a thoroughbred horse in action. The picture is going to tell the story so it needs to be very eye-catching.

Our slogan should also be included on the website, "Experience the thrill of owning a Racehorse."
Should not have
• cartoons, artsy pictures, pictures of Steeplechase horses or "jumpers." This partnership is for racehorses only, there is not jumping involved with the horses.

```html
<!DOCTYPE html>
<html lang="en">
<head>
<meta charset="utf-8">
<title>Glimmer of Laurel Partners — Thoroughbred Racing Partnerships</title>
<link href="https://fonts.googleapis.com/css2?family=PT+Sans+Narrow:wght@400;700&family=PT+Sans:wght@400;700&family=Arimo:wght@400;700&display=swap" rel="stylesheet">
<style>
:root{
  --navy:#0b3a6e;
  --navy-deep:#033a70;
  --link:#1a5a9c;
  --ink:#1d1d1d;
  --body:#3a3a3a;
  --rule:#d4d4d4;
  --nav-dark:#141414;
  --nav-active:#6f9cc0;
  --panel:#f1f1f1;
  --date:#7a7a7a;
}
*{margin:0;padding:0;box-sizing:border-box}
html,body{width:1034px;height:1200px;overflow:hidden}
body{position:relative;background:#fff;font-family:"Arimo",Arial,sans-serif;color:var(--body)}
.abs{position:absolute}

/* hero */
.hero{left:0;top:0;width:1034px;height:556px;
  background:linear-gradient(180deg,#233e63 0%,#4d6d90 22%,#8ea7bd 45%,#a9c197 72%,#86b867 100%)}
.hero-photo{left:130px;top:118px;width:660px;height:438px;
  background:radial-gradient(ellipse at 45% 55%,#3a5aa8 0%,#56607a 40%,rgba(90,96,110,.55) 70%,rgba(120,140,120,0) 100%)}
.brand{left:121px;top:17px;width:158px;height:84px;background:#fff;border-radius:3px 0 0 3px;
  display:flex;align-items:center;justify-content:center;flex-direction:column;
  font-family:"PT Sans",sans-serif;font-weight:700;color:var(--navy);line-height:1}
.brand .mark{font-size:40px;letter-spacing:1px}
.brand .sub{font-size:15px;margin-top:3px}
.tagline{left:673px;top:12px;font-family:"PT Sans",sans-serif;font-size:12.5px;line-height:20px;color:#e6edf4;letter-spacing:.3px}
.tagline .second{color:#c8d6e4}
.nav{left:279px;top:60px;width:634px;height:41px;border-radius:0 4px 4px 0;
  background:linear-gradient(180deg,#3a3a3a 0%,#1a1a1a 45%,#050505 100%);display:flex;padding-left:85px}
.nav a{display:flex;align-items:center;padding:0 18px;height:41px;color:#fff;text-decoration:none;
  font-family:"PT Sans",sans-serif;font-weight:700;font-size:11.5px;border-right:1px solid #333}
.nav a:last-child{border-right:0}
.nav a.active{background:var(--nav-active)}
.slogan{right:125px;top:138px;text-align:right;font-family:"PT Sans Narrow",sans-serif;font-weight:700;
  font-size:37px;line-height:38px;color:#fff;text-shadow:0 1px 3px rgba(0,0,0,.35)}
.slogan span{display:block}
.slogan .l1{margin-right:103px}
.arrow{top:286px}
.dots{left:834px;top:525px;display:flex;gap:9px}
.dots i{width:13px;height:13px;border-radius:50%;background:#e8ecee;display:block;border:1px solid #c9d0d4}
.dots i.on{background:#4c88b8;border:2px solid #dce6ee}

/* welcome */
.welcome{left:0;top:556px;width:1034px;height:234px;background:#fbfbfb}
.welcome h1{left:123px;top:36px;width:464px;padding-bottom:10px;border-bottom:1px dotted #cfcfcf;
  font-family:"PT Sans Narrow",sans-serif;font-weight:400;font-size:21px;color:var(--ink)}
.welcome h1 b{color:var(--navy);font-weight:700}
.welcome .lead{left:123px;top:83px;font-size:10.5px;font-weight:700;color:var(--ink)}
.welcome .copy{left:123px;top:104px;width:467px;font-size:10px;line-height:16px;text-align:justify;letter-spacing:.2px}
.readmore{font-size:10.5px;font-weight:700;color:var(--link);text-decoration:none}
.welcome .readmore{left:526px;top:200px}
.video{left:613px;top:32px;width:300px;height:181px;background:linear-gradient(180deg,#b7bfc6,#dfe3e6 60%,#cfd5da)}
.video-title{left:0;width:300px;top:72px;text-align:center;font-family:"PT Sans",sans-serif;font-weight:700;color:var(--navy);font-size:26px;line-height:1}
.video-title small{display:block;font-size:14px;letter-spacing:3px;margin-top:4px}
.controls{left:0;top:154px;width:300px;height:27px;background:linear-gradient(#2a2a2a,#0c0c0c)}
.progress{left:0;top:154px;width:300px;height:4px;background:#3b3b3b}
.progress i{display:block;width:25px;height:4px;background:#c9271f}
.time{left:73px;top:166px;font-size:8px;color:#ddd}

/* columns */
.cols{left:0;top:790px;width:1034px;height:244px;background:var(--panel);border-top:1px solid #e2e2e2}
.col{top:20px;width:240px}
.col h2{font-family:"PT Sans Narrow",sans-serif;font-weight:400;font-size:19.5px;color:var(--ink);padding-bottom:3px;border-bottom:1px dotted #c8c8c8}
.col h2 em{font-style:normal;color:var(--link)}
.divider{top:15px;width:1px;height:220px;background:#dcdcdc}
.about p{font-size:10px;line-height:13.8px;margin-top:7px;color:#333}
.about ul{list-style:none;margin-top:14px}
.about li{font-size:9.5px;font-weight:700;color:var(--ink);line-height:16.5px;padding-left:13px;position:relative}
.about li:before{content:"»";position:absolute;left:0;font-weight:400;color:#555}
.about li.hl{color:var(--navy)}
.news-item{display:flex;gap:17px;padding:9px 0;border-bottom:1px dotted #c8c8c8;height:57px}
.news-item:last-child{border-bottom:0}
.date{width:34px;height:34px;border-radius:3px;background:var(--date);color:#fff;text-align:center;font-weight:700;flex:none}
.date b{display:block;font-size:16px;line-height:19px}
.date span{display:block;font-size:8.5px;line-height:10px}
.news-item p{font-size:10px;line-height:13.8px;color:#333}
.testi{display:flex;gap:16px;margin-top:10px}
.portrait{width:64px;height:64px;border:1px solid #c8c8c8;background:linear-gradient(160deg,#d7dde3,#8d96a1);flex:none;margin-left:4px}
.testi p{font-size:10px;line-height:16px;color:#333;letter-spacing:.2px}
.testi .q{color:#bbb;font-size:14px;font-family:Georgia,serif}
.who{margin:14px 0 0 84px;font-size:11px;font-weight:700;line-height:17px;color:#000}
.who span{color:var(--navy);display:block}
.col .readmore{position:absolute;top:211px;right:6px}

/* footer */
.footer{left:0;top:1034px;width:1034px;height:166px;background:var(--navy-deep);border-top:3px solid #5c86ad;color:#fff}
.footer h3{font-family:"PT Sans",sans-serif;font-weight:700;font-size:13px;padding-bottom:6px;border-bottom:1px solid #2f5e8d;letter-spacing:.3px}
.fcol{top:28px}
.fsep{top:22px;width:1px;height:128px;background:#1f4f80}
.links{display:grid;grid-template-columns:118px 90px;row-gap:10px;margin-top:9px}
.links a{font-size:9.5px;color:#fff;text-decoration:none;padding-left:14px;position:relative;line-height:15px}
.links a:before{content:"›";position:absolute;left:0;top:-2px;font-size:14px;font-weight:700}
.newsletter p{font-size:9.5px;line-height:14px;margin-top:8px;color:#e5ecf3}
.email{width:173px;height:22px;background:#fff;border-radius:2px;margin-top:9px;font-size:9px;color:#777;padding:5px 7px}
.subscribe{margin:7px 0 0 105px;width:68px;height:20px;border-radius:2px;background:linear-gradient(#8db7d6,#5687b2);font-size:9.5px;font-weight:700;text-align:center;line-height:20px}
.contact li{list-style:none;display:flex;gap:9px;font-size:9.5px;line-height:14px;margin-top:8px;color:#e5ecf3}
.contact li svg{flex:none;margin-top:1px}
.fbrand{left:780px;top:26px;width:130px;text-align:center}
.fbrand .mark{font-family:"PT Sans",sans-serif;font-weight:700;font-size:30px;line-height:1;color:#c9d7e6}
.fbrand .mark small{display:block;font-size:13px;margin-top:2px}
.fbrand .copy{font-size:9.5px;margin-top:12px;color:#e5ecf3}
.social{display:flex;gap:10px;justify-content:center;margin-top:17px}
.social i{display:block;width:26px;height:26px;border-radius:50%;background:#aebdcc}
</style>
</head>
<body>

<header>
  <div class="abs hero" role="img" aria-label="Racing backdrop with a blurred green turf and blue sky"></div>
  <div class="abs hero-photo" role="img" aria-label="Photograph of a jockey in blue silks celebrating on a grey thoroughbred racehorse"></div>
  <div class="abs brand"><span class="mark">GOL</span><span class="sub">PARTNERS</span></div>
  <div class="abs tagline"><div>GLIMMER OF LAUREL</div><div class="second">THOROUGHBRED RACING PARTNERSHIPS</div></div>
  <nav class="abs nav">
    <a class="active" href="#">HOME</a><a href="#">ABOUT US</a><a href="#">OWNERSHIP</a><a href="#">STABLE ROSTER</a><a href="#">NEWS</a><a href="#">CONTACT US</a>
  </nav>
  <div class="abs slogan"><span class="l1">Experience the thrill</span><span>of owning a Racehorse.</span></div>
  <svg class="abs arrow" style="left:120px" width="16" height="30" viewBox="0 0 16 30"><path d="M15 1 1 15l14 14" fill="none" stroke="#e9eef2" stroke-width="1.5" opacity=".8"/></svg>
  <svg class="abs arrow" style="left:897px" width="16" height="30" viewBox="0 0 16 30"><path d="M1 1l14 14L1 29" fill="none" stroke="#e9eef2" stroke-width="1.5" opacity=".8"/></svg>
  <div class="abs dots"><i class="on"></i><i></i><i></i><i></i></div>
</header>

<section class="abs welcome">
  <h1 class="abs">Welcome to <b>GOL</b></h1>
  <p class="abs lead">Glimmer of Laurel Partners is a management group who buys horses and races</p>
  <p class="abs copy">Glimmer of Laurel Partners is a management group who buys horses and races them on both the West and East coasts. The premise of the business is for an investment as little as $500, anyone can be a partner and own a percentage of a horse(s). This is a low cost way of getting involved in the exciting sport of Thoroughbred Racing, without shouldering the heavy financial responsibility.</p>
  <a class="abs readmore" href="#">Read More »</a>
  <div class="abs video" role="img" aria-label="Introductory video player">
    <svg class="abs" style="left:132px;top:48px" width="36" height="36" viewBox="0 0 36 36"><circle cx="18" cy="18" r="17" fill="#fff" opacity=".85"/><path d="M14 11v14l12-7z" fill="#0b3a6e"/></svg>
    <div class="abs video-title">GOL<small>PARTNERS</small></div>
    <div class="abs controls"></div>
    <div class="abs progress"><i></i></div>
    <svg class="abs" style="left:18px;top:165px" width="120" height="12" viewBox="0 0 120 12"><rect x="0" y="1" width="3" height="10" fill="#ddd"/><rect x="6" y="1" width="3" height="10" fill="#ddd"/><path d="M35 4h3l4-3v10l-4-3h-3z" fill="#ddd"/></svg>
    <div class="abs time">0:07 / 2:54</div>
    <svg class="abs" style="left:210px;top:165px" width="82" height="12" viewBox="0 0 82 12"><circle cx="6" cy="6" r="5" fill="#bbb"/><rect x="26" y="3" width="12" height="7" fill="#bbb"/><circle cx="57" cy="6" r="5" fill="none" stroke="#bbb" stroke-width="2.5"/><path d="M70 4V1h3M79 1h3v3M82 8v3h-3M73 11h-3V8" fill="none" stroke="#bbb" stroke-width="1.5"/></svg>
  </div>
</section>

<section class="abs cols">
  <div class="abs col about" style="left:123px">
    <h2>Shortly <em>About Us</em></h2>
    <p>Duis autem veli eum iriure dolor in hendrerit in vulpu tate velit esse molestie consequat, vel illum dolorel feugiatmul nulla facilisis at vero eros et accumsano et iusto odio dignissim qui blandit praesent luptatuli zrilopil delenit augue duis dolore te feugait nullamol facilisi.</p>
    <ul><li>Lorem ipsum dolor sit amet, consectetuer</li><li class="hl">Duis autem veli eum iriure dolor in hendrerit</li><li>Blandit praesent luptatuli zrilopil delenit</li></ul>
    <a class="readmore" href="#">Read More »</a>
  </div>
  <div class="abs divider" style="left:379px"></div>
  <div class="abs col news" style="left:397px">
    <h2>Latest <em>News &amp; Events</em></h2>
    <div class="news-item"><div class="date"><b>29</b><span>OCT</span></div><p>Lorem ipsum dolor sit amet, consectetu adipiscing elit, sed diam nonummy nibh consecte nonummy nibh.</p></div>
    <div class="news-item"><div class="date"><b>29</b><span>OCT</span></div><p>Lorem ipsum dolor sit amet, consectetu adipiscing elit, sed diam nonummy nibh consecte nonummy nibh.</p></div>
    <div class="news-item"><div class="date"><b>29</b><span>OCT</span></div><p>Lorem ipsum dolor sit amet, consectetu adipiscing elit, sed diam nonummy nibh consecte nonummy nibh.</p></div>
    <a class="readmore" href="#">Read More »</a>
  </div>
  <div class="abs divider" style="left:654px"></div>
  <div class="abs col testimonial" style="left:672px">
    <h2>Client <em>Testimonial</em></h2>
    <div class="testi"><div class="portrait" role="img" aria-label="Portrait photo of the client"></div>
      <p><span class="q">“</span> Ut wisi enim ad mini veniam, quis nostrud exerci tationullamo corper suscipit lobortis nislutalil uip commodoconsequat. <span class="q">”</span></p></div>
    <div class="who"><span>Mr. Lorem ipsum sit amet</span>Chief Executive</div>
    <a class="readmore" href="#">Read More »</a>
  </div>
</section>

<footer class="abs footer">
  <div class="abs fcol" style="left:123px;width:204px">
    <h3>QUICK LINKS</h3>
    <div class="links"><a href="#">Home</a><a href="#">News</a><a href="#">About Us</a><a href="#">Contact Us</a><a href="#">Ownership</a><span></span><a href="#">Stable Roster</a></div>
  </div>
  <div class="abs fsep" style="left:347px"></div>
  <div class="abs fcol newsletter" style="left:369px;width:179px">
    <h3>NEWSLETTER</h3>
    <p>Subscribe to our newsletter to receive our special offers and more.</p>
    <div class="email">Enter your Email Address here</div>
    <div class="subscribe">SUBSCRIBE</div>
  </div>
  <div class="abs fsep" style="left:565px"></div>
  <div class="abs fcol contact" style="left:586px;width:154px">
    <h3>CONTACT DETAILS</h3>
    <ul>
      <li><svg width="11" height="14" viewBox="0 0 11 14"><path d="M5.5 0A5.5 5.5 0 0 0 0 5.5C0 9 5.5 14 5.5 14S11 9 11 5.5A5.5 5.5 0 0 0 5.5 0zm0 7.5a2 2 0 1 1 0-4 2 2 0 0 1 0 4z" fill="#fff"/></svg>Sed diam nonummy euismod tincidunt ut laor</li>
      <li style="margin-top:13px"><svg width="12" height="12" viewBox="0 0 12 12"><path d="M2.5 0l2 3-1.2 1.3a7 7 0 0 0 4.4 4.4L9 7.5l3 2-1.5 2.3C5 11.5.5 7 0 1.5z" fill="#fff"/></svg>(000)123-4567</li>
      <li style="margin-top:16px"><svg width="12" height="9" viewBox="0 0 12 9"><rect width="12" height="9" fill="#fff"/><path d="M0 0l6 5 6-5" fill="none" stroke="#033a70"/></svg>info@golpartners.example</li>
    </ul>
  </div>
  <div class="abs fsep" style="left:761px"></div>
  <div class="abs fbrand">
    <div class="mark">GOL<small>PARTNERS</small></div>
    <div class="copy">Copyright © 2013 GOL.</div>
    <div class="social"><i></i><i></i><i></i><i></i></div>
  </div>
</footer>

</body>
</html>
```